Brivolt Technologies business card design

We need a business card designed with our new logo. it would be great if the card could communicate it is a technology based company.

Target Market(s)

system integrators

Industry/Entity Type

technology, IOT

Contact Information for Business Card

Name, designation, Address, telephone number, email address

Requirements
Must have
• logo and company name
Nice to have
• something to do with technology

```html
<!DOCTYPE html>
<html lang="en">
<head>
<meta charset="utf-8">
<title>Brivolt Technologies — Business Card</title>
<link href="https://fonts.googleapis.com/css2?family=Open+Sans:wght@400;600;700&display=swap" rel="stylesheet">
<style>
  :root {
    --stage: #3b3b3a;
    --card: #161616;
    --card-shade: #1d1d1d;
    --orange: #f7931e;
    --white: #ffffff;
    --soft: #d9d9d9;
  }
  * { box-sizing: border-box; margin: 0; padding: 0; }
  html, body {
    width: 1200px; height: 801px; overflow: hidden;
    background: var(--stage);
    font-family: "Open Sans", Arial, sans-serif;
  }
  .stage {
    position: relative; width: 1200px; height: 801px;
    display: flex; align-items: center; justify-content: center; gap: 40px;
  }
  .card {
    position: relative; width: 540px; height: 309px;
    background: linear-gradient(135deg, var(--card-shade), var(--card));
    border-bottom: 3px solid var(--orange);
    box-shadow: 0 18px 40px rgba(0,0,0,.45);
    overflow: hidden;
  }
  .brand {
    position: absolute; display: flex; align-items: center; gap: 12px;
    color: var(--white); font-weight: 700; letter-spacing: .04em;
    text-transform: uppercase;
  }
  .brand-square { background: var(--orange); flex: none; }
  .front .brand { left: 34px; top: 48px; font-size: 22px; }
  .front .brand-square { width: 26px; height: 26px; }
  .holder { position: absolute; left: 34px; top: 128px; }
  .holder-name {
    color: var(--orange); font-weight: 700; font-size: 19px;
    text-transform: uppercase; letter-spacing: .02em;
  }
  .holder-role { color: var(--soft); font-size: 13px; margin-top: 2px; }
  .contacts {
    position: absolute; left: 34px; bottom: 30px; list-style: none;
    color: var(--soft); font-size: 13px; line-height: 1.75;
  }
  .contacts li { display: flex; align-items: center; gap: 9px; }
  .contacts svg { width: 12px; height: 12px; fill: var(--orange); flex: none; }
  .address {
    position: absolute; right: 30px; top: 60px; text-align: right;
    color: var(--soft); font-size: 13px; line-height: 1.6;
  }
  .back .brand {
    right: 40px; bottom: 64px; font-size: 30px;
  }
  .back .brand-square { width: 18px; height: 18px; }
</style>
</head>
<body>
<main class="stage">
  <section class="card front" aria-label="Card front">
    <div class="brand"><span class="brand-square"></span>Brivolt Technologies</div>
    <div class="holder">
      <p class="holder-name">Dorian Vell</p>
      <p class="holder-role">President</p>
    </div>
    <ul class="contacts">
      <li><svg viewBox="0 0 12 12"><path d="M3 1l2 2.5-1.2 1.3a7 7 0 0 0 3.4 3.4L8.5 7 11 9l-1.5 2C5 11 1 7 1 2.5z"/></svg>949-555-0187</li>
      <li><svg viewBox="0 0 12 12"><path d="M1 3h10v6H1zM1 3l5 3.5L11 3" /></svg>info@brivolttech.com</li>
      <li><svg viewBox="0 0 12 12"><circle cx="6" cy="6" r="5"/></svg>www.brivolttech.com</li>
    </ul>
    <address class="address">1840 Harbor Crest Way<br>Seacliff CA 92601</address>
  </section>
  <section class="card back" aria-label="Card back">
    <div class="brand"><span class="brand-square"></span>Brivolt Technologies</div>
  </section>
</main>
</body>
</html>
```